Flyer-Design für psychologische Beratungspraxis für Mütter
Vielen herzlichen Dank! Super Kommunikation, alle Änderungswünsche wurden sofort umgesetzt, auch hin und her meinerseits war kein Problem, immer wieder. Schnelle Reaktion, tolle Ideen. Ich bin super zufrieden und würde jederzeit sehr gerne wieder mit brightfoxes zusammenarbeiten! Toller Flyer, ich liebe meinen neuen Flyer! :)
Zielgruppe
Gelassenheitswerkstatt ist eine psychologische Beratungspraxis. Ich unterstütze Mütter, Schwangere und Frauen mit Kinderwunsch bei Herausforderungen rund um Schwangerschaft, Geburt, Mutterschaft, und damit einhergehenden Problemen.
Aufgabenstellung
Text nochmal geringgradig geändert...siehe Datei anbei

```html
<!DOCTYPE html>
<html lang="de">
<head>
<meta charset="utf-8">
<title>Gelassenheitswerkstatt – Flyer</title>
<link rel="stylesheet" href="https://fonts.googleapis.com/css2?family=Open+Sans:wght@400;600;700&family=Roboto:wght@400;700&display=swap">
<style>
  :root {
    --navy: #27307a;
    --green: #3e9a2c;
    --orange: #e9772a;
    --backdrop: #e9ece6;
    --paper-top: #ffffff;
    --paper-bottom: #fdf6d8;
    --fold: #e3e0d0;
    --photo-sky: #6fa6d9;
    --photo-land: #6d7a3c;
    --photo-warm: #f1e6c2;
    --photo-grass: #9b8a4e;
  }
  * { box-sizing: border-box; margin: 0; padding: 0; }
  html, body { width: 1200px; height: 1200px; overflow: hidden; }
  body {
    background: var(--backdrop);
    font-family: "Open Sans", sans-serif;
    color: var(--navy);
    position: relative;
  }
  .flyer {
    position: absolute;
    left: 38px; top: 38px;
    width: 1124px; height: 1124px;
    display: flex;
    box-shadow: 0 4px 18px rgba(0,0,0,0.18);
  }
  .panel {
    position: relative;
    width: 562px; height: 1124px;
    background: linear-gradient(to bottom, var(--paper-top) 0%, var(--paper-top) 45%, var(--paper-bottom) 100%);
  }
  .panel + .panel { border-left: 1px solid var(--fold); }
  .line { position: absolute; left: 0; right: 0; text-align: center; }

  .brand {
    position: absolute; left: 0; right: 0;
    top: 95px;
    display: flex; flex-direction: column; align-items: center; gap: 16px;
  }
  .brand-dot {
    width: 70px; height: 70px; border-radius: 50%;
    background: var(--orange);
  }
  .brand-name {
    font-family: "Open Sans", sans-serif;
    font-weight: 700; font-size: 19px;
    color: var(--navy);
    letter-spacing: 0.5px;
  }

  .tagline { top: 242px; font-size: 19px; letter-spacing: 0.3px; }
  .person { top: 295px; font-size: 20px; font-weight: 700; }
  .role { top: 332px; font-size: 19.5px; line-height: 27px; }
  .portrait {
    position: absolute; left: 132px; top: 406px;
    width: 300px; height: 434px;
    background: linear-gradient(to bottom, var(--photo-sky) 0%, #a9c9e6 45%, var(--photo-land) 62%, #5c6a30 100%);
  }
  .practice-name { top: 858px; font-size: 24px; font-weight: 700; color: var(--green); }
  .address { top: 903px; font-family: "Roboto", sans-serif; font-size: 19.5px; line-height: 27px; }
  .phone { top: 994px; font-family: "Roboto", sans-serif; font-size: 20px; }
  .web { top: 1036px; font-family: "Roboto", sans-serif; font-size: 18.5px; line-height: 27px; }
  .web .accent { color: var(--green); }

  .headline {
    top: 250px;
    font-family: "Roboto", sans-serif; font-weight: 700;
    font-size: 48px; line-height: 60px;
  }
  .headline .and { color: var(--green); }
  .mood-photo {
    position: absolute; left: 53px; top: 466px;
    width: 456px; height: 456px;
  }
  .audience {
    top: 966px;
    font-family: "Roboto", sans-serif;
    font-size: 28.5px; line-height: 40px;
  }
</style>
</head>
<body>
  <div class="flyer">
    <section class="panel panel-back">
      <div class="brand">
        <span class="brand-dot"></span>
        <span class="brand-name">GELASSENHEITSWERKSTATT</span>
      </div>
      <p class="line tagline">SYSTEMISCHE BERATUNG &amp; COACHING</p>
      <p class="line person">Dr. Helena Marquardt</p>
      <p class="line role">Systemische Beraterin (Mitglied der VSBF)<br>Heilpraktikerin für Psychotherapie</p>
      <div class="portrait" role="img" aria-label="Foto der Beraterin an einem Wegweiser auf einem Berg mit Meerblick"></div>
      <p class="line practice-name">Gelassenheitswerkstatt</p>
      <p class="line address">Lindenweg 12<br>Rückgebäude<br>80797 München</p>
      <p class="line phone">0151 248 17 530</p>
      <p class="line web">info@gelassenheits<span class="accent">werkstatt</span>.de<br>www.gelassenheits<span class="accent">werkstatt</span>.de</p>
    </section>

    <section class="panel panel-front">
      <div class="brand">
        <span class="brand-dot"></span>
        <span class="brand-name">GELASSENHEITSWERKSTATT</span>
      </div>
      <h1 class="line headline">Krisenbegleitung<br><span class="and">und</span><br>Lebensberatung</h1>
      <svg class="mood-photo" viewBox="0 0 456 456" role="img" aria-label="Foto einer nachdenklichen Frau, die im Abendlicht zwischen Dünengras sitzt">
        <defs>
          <linearGradient id="mood-fill" x1="0" y1="0" x2="0" y2="1">
            <stop offset="0" stop-color="#f4ecc9"/>
            <stop offset="0.5" stop-color="var(--photo-warm)"/>
            <stop offset="1" stop-color="var(--photo-grass)"/>
          </linearGradient>
        </defs>
        <circle cx="228" cy="228" r="222" fill="url(#mood-fill)"/>
        <circle cx="228" cy="228" r="225" fill="none" stroke="var(--green)" stroke-width="3"/>
      </svg>
      <p class="line audience">Psychologische Beratungspraxis<br>für Mütter, Schwangere und<br>Frauen mit Kinderwunsch</p>
    </section>
  </div>
</body>
</html>
```